Brightway Coordination Group Business card

We wish to have a professional Business card to present to large Corporate CEO's ASAP.

Our web site helps explain our business www.brightwaycg.org

Brightway Coordination Group was established after we discovered how difficult it is to organise outsourced services while heading up a business or company.

We act as a facilitator for businesses who don't have the desire, expertise or recourses to manage their own systems and meet all their requirements.

We provide an all in one facility management solution for all types of businesses. We manage schedules, contractors and costs on behalf of businesses and their needs and wants.

Having an extensive network ensures we are able to connect businesses with the right service providers.

Target Market(s)

Company CEO

Industry/Entity Type

Business

Font styles to use
Sans Serif

Colors
33a6d7
f9fdfe
0355a3

Requirements
Must have
• professional design
Nice to have
• colours to match logo

```html
<!DOCTYPE html>
<html lang="en">
<head>
<meta charset="utf-8">
<title>Brightway Coordination Group – Business Card</title>
<link rel="stylesheet" href="https://fonts.googleapis.com/css2?family=Lato:wght@300;400;700&display=swap">
<style>
  :root {
    --backdrop: #3a3a3a;
    --card: #f9fdfe;
    --card-edge: #e4e8ea;
    --sky: #33a6d7;
    --navy: #0355a3;
    --ink: #1d1d1d;
    --muted: #555b60;
  }
  * { box-sizing: border-box; margin: 0; padding: 0; }
  html, body {
    width: 1200px; height: 997px; overflow: hidden;
    background: var(--backdrop);
    font-family: "Lato", Arial, sans-serif;
  }
  .stage {
    position: relative; width: 1200px; height: 997px;
  }
  .card {
    position: absolute; left: 280px;
    width: 640px; height: 366px;
    background: var(--card);
    border: 1px solid var(--card-edge);
    border-radius: 26px;
  }
  .card--front { top: 92px; }
  .card--back  { top: 540px; }

  .brand {
    position: absolute;
    display: flex; align-items: center; gap: 14px;
  }
  .brand__dot {
    width: 34px; height: 34px; border-radius: 50%;
    background: var(--navy);
    flex: none;
  }
  .brand__name {
    font-weight: 700; font-size: 24px; letter-spacing: 1.5px;
    text-transform: uppercase; color: var(--navy);
    white-space: nowrap;
  }
  .card--front .brand { left: 50%; top: 50%; transform: translate(-50%, -50%); }
  .card--back .brand { left: 90px; top: 62px; }
  .card--back .brand__name { font-size: 21px; }
  .card--back .brand__dot { width: 30px; height: 30px; }

  .holder {
    position: absolute; right: 48px; top: 142px;
    font-weight: 400; font-size: 22px; letter-spacing: 1px;
    text-transform: uppercase; color: var(--navy);
  }
  .holder__first { font-weight: 300; }
  .holder__rule {
    position: absolute; left: 0; right: 36px; top: 178px;
    height: 2px; background: var(--ink);
  }
  .contact {
    position: absolute; left: 48px; top: 232px;
    border-top: 2px solid var(--ink);
    padding-top: 12px; width: 300px;
    list-style: none;
  }
  .contact__item {
    display: flex; align-items: center; gap: 12px;
    font-weight: 700; font-size: 15px; color: var(--muted);
    line-height: 30px;
  }
  .contact__icon { width: 18px; height: 18px; flex: none; }
</style>
</head>
<body>
<main class="stage">
  <section class="card card--front" aria-label="Card front">
    <div class="brand">
      <span class="brand__dot"></span>
      <span class="brand__name">Brightway Coordination Group</span>
    </div>
  </section>

  <section class="card card--back" aria-label="Card back">
    <div class="brand">
      <span class="brand__dot"></span>
      <span class="brand__name">Brightway Coordination Group</span>
    </div>
    <p class="holder"><span class="holder__first">Martin</span> Calloway</p>
    <div class="holder__rule"></div>
    <ul class="contact">
      <li class="contact__item">
        <svg class="contact__icon" viewBox="0 0 20 20" aria-hidden="true">
          <path fill="#0355a3" d="M3 7c0-2 2-3 7-3s7 1 7 3v1h-3V6.5c-1-.5-2.5-.7-4-.7s-3 .2-4 .7V8H3z"/>
          <path fill="#0355a3" d="M5 9h10l2 7H3z"/>
          <circle cx="10" cy="12.5" r="2" fill="#f9fdfe"/>
        </svg>
        0400 123 987
      </li>
      <li class="contact__item">
        <svg class="contact__icon" viewBox="0 0 20 20" aria-hidden="true">
          <g fill="none" stroke="#33a6d7" stroke-width="2.2" stroke-linecap="round">
            <path d="M8.5 11.5l3-3"/>
            <path d="M9 6l1.5-1.5a3 3 0 014.2 4.2L13 10.4"/>
            <path d="M11 14l-1.5 1.5a3 3 0 01-4.2-4.2L7 9.6"/>
          </g>
        </svg>
        www.brightwaycg.org
      </li>
      <li class="contact__item">
        <svg class="contact__icon" viewBox="0 0 20 20" aria-hidden="true">
          <rect x="2" y="4" width="16" height="12" rx="1" fill="#0355a3"/>
          <path d="M2.5 5l7.5 6 7.5-6" fill="none" stroke="#f9fdfe" stroke-width="1.4"/>
        </svg>
        martin@brightwaycg.org
      </li>
    </ul>
  </section>
</main>
</body>
</html>
```